Business Card Design for Marketing Firm

Looking for business card design for higher end marketing firm. Clean but impressionable/trendy. We are a marketing firm that represents manufacturers in the foodservice equipment and supply industry. Our customers are end users such has hotels, restaurants, country clubs, convention centers and casinos as well as distributors of restaurants supplies and equipment, and manufacturers of foodservice equipment and supplies.
Target Market(s)
Hotels, Restaurants, Supply & Equipment Distributors, Foodservice Manufacturers
Industry/Entity Type
Foodservice/Hospitality
Contact Information for Business Card
Name, Title, Contact Number, Email, Website, Social Media, Address
Requirements
Must have
- Clean & Simple but Serious and Impressionable

```html
<!DOCTYPE html>
<html lang="en">
<head>
<meta charset="utf-8">
<title>Meridian Foodservice Reps – Business Card</title>
<link href="https://fonts.googleapis.com/css2?family=Cinzel:wght@500&family=Montserrat:wght@500;800&display=swap" rel="stylesheet">
<style>
  :root {
    --navy: #2a2874;
    --white: #ffffff;
    --ink: #3a3a44;
    --page: #ecebef;
  }
  * { box-sizing: border-box; margin: 0; padding: 0; }
  html, body { width: 1200px; height: 834px; overflow: hidden; }
  body {
    background: var(--page);
    position: relative;
    font-family: "Montserrat", sans-serif;
  }
  .card {
    position: absolute;
    top: 262px;
    width: 540px;
    height: 310px;
    border-radius: 22px;
    overflow: hidden;
    box-shadow: 0 6px 18px rgba(20, 20, 60, 0.18);
  }
  .card--front { left: 40px; background: var(--white); }
  .card--back { left: 620px; background: var(--navy); }

  .front-swoosh { position: absolute; inset: 0; }

  .brand {
    position: absolute;
    display: flex;
    align-items: center;
    gap: 10px;
    font-family: "Cinzel", serif;
    font-weight: 500;
    letter-spacing: 0.04em;
    line-height: 1.15;
  }
  .brand__dot {
    flex: none;
    border-radius: 50%;
  }
  .card--front .brand {
    left: 92px; top: 112px;
    color: var(--navy);
    font-size: 17px;
  }
  .card--front .brand__dot { width: 16px; height: 16px; background: var(--navy); }

  .divider {
    position: absolute;
    left: 292px; top: 54px;
    width: 1.5px; height: 204px;
    background: var(--navy);
  }
  .details {
    position: absolute;
    left: 312px; top: 60px;
    color: var(--ink);
    font-size: 12.5px;
    line-height: 1.5;
  }
  .details__name {
    font-weight: 800;
    font-size: 19px;
    color: var(--navy);
    letter-spacing: 0.02em;
    line-height: 1.2;
  }
  .details__title { margin-bottom: 8px; }
  .details__address { margin-bottom: 8px; }
  .contact-list { list-style: none; }
  .contact-list li { display: flex; align-items: center; gap: 7px; }
  .contact-list svg { width: 11px; height: 11px; flex: none; fill: var(--navy); }

  .card--back .brand {
    left: 0; right: 0; top: 112px;
    justify-content: center;
    color: var(--white);
    font-size: 27px;
    text-align: center;
  }
  .card--back .brand__dot { width: 22px; height: 22px; background: var(--white); }
  .social {
    position: absolute;
    left: 0; right: 0; top: 218px;
    display: flex;
    justify-content: center;
    gap: 6px;
  }
  .social span {
    width: 16px; height: 16px;
    border: 1.4px solid var(--white);
    border-radius: 50%;
  }
</style>
</head>
<body>

<section class="card card--front" aria-label="Card front">
  <svg class="front-swoosh" viewBox="0 0 540 310" preserveAspectRatio="none" aria-hidden="true">
    <path d="M0 0 H34 C70 80 110 150 160 200 C210 250 260 285 300 310 H0 Z" fill="var(--navy)"/>
    <path d="M18 0 C52 78 92 150 142 202 C190 252 240 286 280 310" fill="none" stroke="var(--white)" stroke-width="3"/>
  </svg>

  <div class="brand">
    <span class="brand__dot"></span>
    <span>Meridian<br>Foodservice Reps</span>
  </div>

  <div class="divider"></div>

  <div class="details">
    <p class="details__name">LENA CORVIN</p>
    <p class="details__title">Managing Director</p>
    <p class="details__address">42 Alder Court, Suite 210<br>Brookfield, CO 80455</p>
    <ul class="contact-list">
      <li><svg viewBox="0 0 12 12"><path d="M2.5 1 L4.5 1 L5.3 3.6 L4 4.6 C4.7 6 5.9 7.3 7.4 8 L8.4 6.7 L11 7.5 L11 9.5 C11 10.3 10.3 11 9.5 11 C5 11 1 7 1 2.5 C1 1.7 1.7 1 2.5 1 Z"/></svg>5550102233</li>
      <li><svg viewBox="0 0 12 12"><path d="M3 0.5 H9 C9.6 0.5 10 0.9 10 1.5 V10.5 C10 11.1 9.6 11.5 9 11.5 H3 C2.4 11.5 2 11.1 2 10.5 V1.5 C2 0.9 2.4 0.5 3 0.5 Z M3.2 1.8 V9.2 H8.8 V1.8 Z"/></svg>5550104488</li>
      <li><svg viewBox="0 0 12 12"><path d="M0.5 2 H11.5 V10 H0.5 Z M1.5 3 L6 6.5 L10.5 3 Z"/></svg>hello@meridianreps.com</li>
      <li><svg viewBox="0 0 12 12"><path d="M6 0.5 A5.5 5.5 0 1 0 6 11.5 A5.5 5.5 0 1 0 6 0.5 Z M1.8 6 H10.2 M6 1 V11" stroke="var(--white)" stroke-width="0.8"/></svg>www.meridianreps.com</li>
    </ul>
  </div>
</section>

<section class="card card--back" aria-label="Card back">
  <div class="brand">
    <span class="brand__dot"></span>
    <span>Meridian<br>Foodservice Reps</span>
  </div>
  <div class="social" aria-label="Social media links">
    <span></span><span></span><span></span><span></span><span></span>
  </div>
</section>

</body>
</html>
```